TL - business card

Tallow Partners is an insurance brokerage firm, inovative, proactive, vigorous, which aims to become the leader of the insurance brokers in Anfrica. We should like to get some designs which should be avoided also in Gray / Metallic for the Administration and Orange / Blue for the Managers (ike in the picture sent). The Blue / Green logo is not the correct one, but the source of the file. Please adjust the color accordingly for the business cards. 1 / Orange / Blue 2 / Gray / Metallic We want something classic but which is transmitted strenght, inovation, modernity and most of all, rapidity. We want something start-up like, very punchy and catching eye remaining profesional at the same time. Name: Dorian Whitlock Function: Managing Director Address: N ° 17/18 Rua Veloso - R / C 2B Direita - Bairro Mutamba - Luanda Tel: (+244) 947 582 316 Email: dorian.whitlock@tallow-p.example Website: www.tallow-p. example We want classic in the front and creative, colorfull at the back. The cards will be printed in relief, with very high quality of paper.
Insurance Broker
Colors
Designer to choose colors to be used in the design.

```html
<!DOCTYPE html>
<html lang="en">
<head>
<meta charset="utf-8">
<title>Tallow Partners – Business Card</title>
<link href="https://fonts.googleapis.com/css2?family=Roboto:wght@400;500;700&display=swap" rel="stylesheet">
<style>
  :root {
    --green: #009a44;
    --blue: #29a3df;
    --ink: #4a4a4a;
    --paper: #ffffff;
    --stage: #e9eaec;
    --rule: #c9c9c9;
  }
  * { margin: 0; padding: 0; box-sizing: border-box; }
  html, body {
    width: 1200px; height: 960px; overflow: hidden;
    background: var(--stage);
    font-family: "Roboto", Arial, sans-serif;
  }
  .canvas {
    position: relative; width: 1200px; height: 960px;
  }
  .card {
    position: absolute; left: 240px;
    width: 720px; height: 410px;
    box-shadow: 0 6px 18px rgba(0,0,0,.18);
    overflow: hidden;
  }
  /* Back of card */
  .card-back { top: 45px; background: var(--green); }
  .back-mark {
    position: absolute; left: 0; right: 0; top: 140px;
    display: flex; align-items: center; justify-content: center; gap: 16px;
  }
  .mark-dot {
    width: 44px; height: 44px; border-radius: 50%;
    border: 5px solid var(--paper);
  }
  .back-name {
    color: var(--paper); font-weight: 700; font-size: 40px; letter-spacing: .5px;
  }
  .back-web {
    position: absolute; left: 0; right: 0; top: 250px; text-align: center;
    color: var(--paper); font-size: 17px; letter-spacing: 7px;
  }
  /* Front of card */
  .card-front { top: 505px; background: var(--paper); }
  .brand {
    position: absolute; left: 40px; top: 120px; width: 360px;
    display: flex; align-items: center; gap: 12px;
  }
  .brand-dot {
    width: 40px; height: 40px; border-radius: 50%;
    border: 5px solid var(--green); flex: none;
  }
  .brand-name {
    color: var(--green); font-weight: 700; font-size: 34px; white-space: nowrap;
  }
  .divider {
    position: absolute; left: 420px; top: 40px; width: 2px; height: 200px;
    background: linear-gradient(var(--paper), var(--rule) 30%, var(--rule) 70%, var(--paper));
  }
  .contact { position: absolute; left: 445px; top: 46px; width: 260px; }
  .contact-name { color: var(--green); font-weight: 700; font-size: 23px; }
  .contact-role { color: var(--blue); font-weight: 500; font-size: 15px; margin: 2px 0 8px 10px; }
  .contact-address { color: var(--ink); font-size: 13.5px; line-height: 1.4; margin-left: 22px; }
  .contact-lines { margin: 12px 0 0 22px; list-style: none; }
  .contact-lines li {
    color: var(--ink); font-size: 13px; line-height: 1.7;
    display: flex; align-items: center; gap: 8px; white-space: nowrap;
  }
  .contact-lines svg { width: 14px; height: 14px; fill: var(--green); flex: none; }
  .accent-band {
    position: absolute; right: 0; top: 272px; width: 150px; height: 32px;
    background: var(--blue);
  }
  .accent-dot {
    position: absolute; right: 126px; top: 276px; width: 24px; height: 24px;
    border-radius: 50%; border: 3px solid var(--green); background: var(--paper);
  }
  .web-band {
    position: absolute; left: 0; right: 0; top: 304px; height: 48px;
    background: var(--green); display: flex; align-items: center; justify-content: center;
  }
  .web-band span { color: var(--paper); font-size: 17px; letter-spacing: 7px; }
</style>
</head>
<body>
<main class="canvas">
  <section class="card card-back" aria-label="Card back">
    <div class="back-mark">
      <span class="mark-dot"></span>
      <span class="back-name">Tallow Partners</span>
    </div>
    <p class="back-web">www.tallow-p. example</p>
  </section>

  <section class="card card-front" aria-label="Card front">
    <div class="brand">
      <span class="brand-dot"></span>
      <span class="brand-name">Tallow Partners</span>
    </div>
    <div class="divider"></div>
    <div class="contact">
      <h1 class="contact-name">Dorian Whitlock</h1>
      <p class="contact-role">Managing Director</p>
      <p class="contact-address">N ° 17/18 Rua Veloso<br>R / C 2B Direita<br>Bairro Mutamba, Luanda</p>
      <ul class="contact-lines">
        <li>
          <svg viewBox="0 0 24 24" aria-hidden="true"><path d="M6.6 10.8a15.1 15.1 0 0 0 6.6 6.6l2.2-2.2a1 1 0 0 1 1-.25 11.4 11.4 0 0 0 3.6.57 1 1 0 0 1 1 1V20a1 1 0 0 1-1 1A17 17 0 0 1 3 4a1 1 0 0 1 1-1h3.5a1 1 0 0 1 1 1c0 1.25.2 2.45.57 3.57a1 1 0 0 1-.25 1z"/></svg>
          (+244) 947 582 316
        </li>
        <li>
          <svg viewBox="0 0 24 24" aria-hidden="true"><path d="M2 5h20v14H2z M4 7v.5l8 5 8-5V7l-8 5z" fill-rule="evenodd"/></svg>
          dorian.whitlock@tallow-p.example
        </li>
      </ul>
    </div>
    <div class="accent-band"></div>
    <span class="accent-dot"></span>
    <div class="web-band"><span>www.tallow-p. example</span></div>
  </section>
</main>
</body>
</html>
```